Business Card Design

Just looking for a good designs that looks good with our company logo. I'd like it to be simple and to the point. Just including contact information, our logo, and my name somewhere on the card so future clients know who they're contacting, and a couple services offered. The two images I attached are pictures of our logo. I don't care which color they they are, I just attached both images to give a reference of logo colors depending on the color of the card.
Names: Carl Whitby
Phone: 816-555-0147
Email: greenstripeyard@fernmail.test
Services offered:
Mowing
Fertilization
Aeration
Bed & tree maintenance
and more.
Business
Names: Carl Whitby
Phone: 816-555-0147
(no website)

```html
<!DOCTYPE html>
<html lang="en">
<head>
<meta charset="utf-8">
<title>Green Stripe Yard LLC — Business Card</title>
<link rel="stylesheet" href="https://fonts.googleapis.com/css2?family=Raleway:wght@300;400;600&display=swap">
<style>
  :root {
    --page-bg: #e9e9e7;
    --card-dark-top: #736867;
    --card-dark-bottom: #4b4342;
    --card-band: #e6e6e6;
    --text-light: #f3f0ef;
    --text-muted: #d6cfce;
    --text-soft: #b4abaa;
    --band-text: #8a8484;
    --icon-fill: #8f8a8a;
    --badge-ring: rgba(255, 255, 255, 0.22);
    --badge-face: #efedeb;
    --brand-ink: #3a3f4a;
    --rule: rgba(255, 255, 255, 0.18);
  }
  * { box-sizing: border-box; margin: 0; padding: 0; }
  html, body {
    width: 1200px;
    height: 782px;
    overflow: hidden;
    background: var(--page-bg);
    font-family: "Raleway", sans-serif;
  }
  .stage {
    width: 1200px;
    height: 782px;
    display: flex;
    align-items: center;
    justify-content: center;
  }
  .business-card {
    position: relative;
    width: 400px;
    height: 700px;
    overflow: hidden;
    box-shadow: 0 4px 14px rgba(0, 0, 0, 0.18);
    background: var(--card-band);
  }
  .card-face {
    position: absolute;
    inset: 0 0 81px 0;
    background: radial-gradient(ellipse 85% 55% at 50% 22%, var(--card-dark-top) 0%, var(--card-dark-bottom) 100%);
  }
  .brand-badge {
    position: absolute;
    left: 50%;
    top: 222px;
    width: 194px;
    height: 194px;
    margin: -97px 0 0 -97px;
    border-radius: 50%;
    background: var(--badge-ring);
    display: flex;
    align-items: center;
    justify-content: center;
  }
  .brand-badge-face {
    width: 166px;
    height: 166px;
    border-radius: 50%;
    background: var(--badge-face);
    display: flex;
    align-items: center;
    justify-content: center;
    text-align: center;
  }
  .brand-name {
    font-weight: 600;
    font-size: 22px;
    line-height: 1.1;
    letter-spacing: 1px;
    color: var(--brand-ink);
  }
  .identity {
    position: absolute;
    right: 82px;
    top: 346px;
    text-align: right;
  }
  .person-name {
    font-size: 29px;
    color: var(--text-light);
    line-height: 1;
    white-space: nowrap;
  }
  .person-name .first { font-weight: 300; }
  .person-name .last { font-weight: 400; letter-spacing: 0.5px; }
  .company-name {
    margin-top: 6px;
    font-size: 10px;
    letter-spacing: 0.6px;
    color: var(--text-muted);
  }
  .services {
    position: absolute;
    right: 82px;
    top: 470px;
    list-style: none;
    text-align: right;
    padding-top: 14px;
    border-top: 1px solid var(--rule);
    width: 190px;
  }
  .service-item {
    font-size: 11px;
    line-height: 19px;
    letter-spacing: 0.8px;
    color: var(--text-soft);
    text-transform: uppercase;
  }
  .contact-band {
    position: absolute;
    left: 0;
    right: 0;
    bottom: 0;
    height: 81px;
    background: var(--card-band);
    padding: 14px 0 0 34px;
  }
  .contact-line {
    display: flex;
    align-items: center;
    height: 27px;
    font-size: 13px;
    color: var(--band-text);
  }
  .contact-icon {
    width: 20px;
    height: 20px;
    margin-right: 13px;
    flex: none;
  }
</style>
</head>
<body>
<main class="stage">
  <article class="business-card">
    <div class="card-face">
      <div class="brand-badge">
        <div class="brand-badge-face">
          <span class="brand-name">GREEN<br>STRIPE</span>
        </div>
      </div>
      <div class="identity">
        <p class="person-name"><span class="first">carl</span> <span class="last">WHITBY</span></p>
        <p class="company-name">GREEN STRIPE YARD LLC</p>
      </div>
      <ul class="services">
        <li class="service-item">Mowing</li>
        <li class="service-item">Fertilization</li>
        <li class="service-item">Aeration</li>
        <li class="service-item">Bed &amp; tree maintenance</li>
        <li class="service-item">and more</li>
      </ul>
    </div>
    <footer class="contact-band">
      <p class="contact-line">
        <svg class="contact-icon" viewBox="0 0 20 20" aria-hidden="true">
          <circle cx="10" cy="10" r="10" fill="var(--icon-fill)"/>
          <rect x="5" y="6.5" width="10" height="7" fill="none" stroke="#fff" stroke-width="1.2"/>
          <path d="M5 6.5 L10 10.5 L15 6.5" fill="none" stroke="#fff" stroke-width="1.2"/>
        </svg>
        greenstripeyard@fernmail.test
      </p>
      <p class="contact-line">
        <svg class="contact-icon" viewBox="0 0 20 20" aria-hidden="true">
          <circle cx="10" cy="10" r="10" fill="var(--icon-fill)"/>
          <path d="M7.2 5.2 L8.8 7.6 L7.8 8.8 Q9 11.2 11.2 12.2 L12.4 11.2 L14.8 12.8 L13.8 14.6 Q8.6 14.4 5.4 6.2 Z" fill="#fff"/>
        </svg>
        816-555-0147
      </p>
    </footer>
  </article>
</main>
</body>
</html>
```